Geschäftspapiere für Fliesenleger - Meisterbetrieb
Zielgruppe
Wir sind ein mittelständischer Fliesenleger - Meisterbetrieb und möchten unsere Geschäftspapiere erneuern. Unsere Kunden sind Privatkunden, Gewerbetreibende sowie Öffentliche Auftraggeber.
Aufgabenstellung
Unser Logo stellen wir Ihnen zur verfügung und soll unverändert bleiben.
Wir benötigen folgende Geschäftspapiere:
- Briefpapier DIN A4
- Notizblock Karriert DIN A4
- Visitenkarten 5,5 x 8,5 cm
- Kuvert DIN lang mit Fenster
- Kuvert DIN C4 mit Fenster
Bei der Farbe Rot handelt es sich um Verkehrsrot RAL 3020
Als Schriftart haben wir uns Helvetica Neue vorgestellt.
Wir bitten jedoch auch um Vorschläge anderer Moderner und gut lesbarer Schriftarten die für Print und Web bestens geeignet sind.
Wir wünschen uns ein Modernes und Schnörkelloses Design. Bei den Dateien habe ich Ihnen ein Stockphoto angehängt um Ihnen zu zeigen wie wir uns ein Cover oder eine Broschüre vorstellen können. Nur um Ihnen unsere Ideen / Vorstellungen näher zu bringen.

```html
<!DOCTYPE html>
<html lang="de">
<head>
<meta charset="utf-8">
<title>Fliesen-Kolbe – Geschäftspapiere</title>
<link href="https://fonts.googleapis.com/css2?family=Arimo:wght@400;700&display=swap" rel="stylesheet">
<style>
:root{
  --red:#cf2219;
  --ink:#111111;
  --paper:#ffffff;
  --stage:#ffffff;
  --window:#ebebeb;
  --grid:#e2e2e2;
  --shadow:0 1px 6px rgba(0,0,0,.16);
}
*{margin:0;padding:0;box-sizing:border-box}
html,body{width:750px;height:1200px;overflow:hidden;background:var(--stage)}
body{position:relative;font-family:"Arimo","Helvetica Neue",Arial,sans-serif;color:var(--ink)}
.sheet,.card,.envelope{position:absolute;background:var(--paper);box-shadow:var(--shadow)}
.abs{position:absolute;white-space:nowrap}
.wordmark{font-weight:700;color:var(--ink);letter-spacing:.2px;line-height:1}
.red{color:var(--red);font-weight:700}
.b{font-weight:700}
.icons{display:inline-block;vertical-align:middle;fill:var(--ink)}

/* letter */
.letter{left:73px;top:83px;width:491px;height:694px}
.letter .wordmark{left:327px;top:73px;font-size:19.5px}
.letter .sender{left:59px;top:124px;font-size:5.6px}
.letter .recipient{left:59px;top:143px;font-size:8.6px;line-height:11px}
.letter .date{left:59px;top:220px;font-size:8.6px}
.letter .subject{left:59px;top:259px;font-size:8.6px;font-weight:700}
.letter .body{position:absolute;left:59px;top:289px;width:350px;font-size:8.6px;line-height:10.9px}
.letter .body p{margin-bottom:10.9px}
.footer{position:absolute;font-size:5.6px;line-height:7.9px}
.footer div{position:absolute;white-space:nowrap}
.letter .footer{left:0;top:645px;width:100%}
.letter .footer .c1{left:58px}
.letter .footer .c2{left:145px}
.letter .footer .c3{left:243px}
.letter .footer .c4{left:369px}
.footer .icons{width:5px;height:5px;margin-right:3px}

/* business cards */
.card-front{left:502px;top:218px;width:198px;height:129px}
.card-front .wordmark{left:34px;top:66px;font-size:19.5px}
.card-back{left:502px;top:370px;width:198px;height:128px}
.card-back .name{left:58px;top:51px;font-size:10px;font-weight:700}
.card-back .role{left:58px;top:63px;font-size:5.6px}
.card-back .co{left:58px;top:81px;font-size:5.6px;line-height:7.9px}
.card-back .contact{left:122px;top:81px;font-size:5.6px;line-height:7.9px}
.card-back .icons{width:5px;height:5px;margin-right:3px}

/* overview row */
.mini{font-size:2px;line-height:2.8px}
.mini .icons{width:2px;height:2px;margin-right:1px}
.sheet-a{left:36px;top:875px;width:179px;height:253px}
.sheet-a .wordmark{left:119px;top:25px;font-size:7.4px}
.sheet-a .sender{left:21px;top:46px}
.sheet-a .footer{left:0;top:235px;width:100%;font-size:2px;line-height:2.8px}
.sheet-a .footer .c1{left:21px}.sheet-a .footer .c2{left:53px}.sheet-a .footer .c3{left:88px}.sheet-a .footer .c4{left:134px}

.mini-front{left:182px;top:923px;width:73px;height:47px}
.mini-front .wordmark{left:12px;top:21px;font-size:7px}
.mini-back{left:182px;top:978px;width:73px;height:47px}
.mini-back .name{left:21px;top:19px;font-size:3.6px;font-weight:700}
.mini-back .role{left:21px;top:24px;font-size:1.8px}
.mini-back .co{left:21px;top:30px}
.mini-back .contact{left:45px;top:30px}

.sheet-b{left:281px;top:875px;width:179px;height:253px}
.sheet-b .wordmark{left:118px;top:25px;font-size:7.4px}
.sheet-b .rule{position:absolute;left:21px;width:55px;height:0;border-top:.5px solid #cfcfcf}
.sheet-b .grid{position:absolute;left:21px;top:39px;width:145px;height:192px;border:.5px solid var(--grid);
  background-image:linear-gradient(var(--grid) .5px,transparent .5px),linear-gradient(90deg,var(--grid) .5px,transparent .5px);
  background-size:4.8px 4.8px}
.sheet-b .footer{left:0;top:235px;width:100%;font-size:2px;line-height:2.8px}
.sheet-b .footer .c1{left:21px}.sheet-b .footer .c2{left:55px}

.env-c4{left:476px;top:853px;width:196px;height:275px}
.env-c4 .wordmark{left:46px;top:24px;font-size:7.4px}
.window{position:absolute;background:var(--window);border-radius:2px}
.env-c4 .window{left:17px;top:50px;width:77px;height:46px}
.window .sender{position:absolute;left:9px;top:6px}
.window .recipient{position:absolute;left:9px;top:12px;font-size:2.6px;line-height:3.4px}
.env-c4 .web{right:17px;top:255px;font-size:2px}

.env-dl{left:526px;top:999px;width:189px;height:94px}
.env-dl .wordmark{left:47px;top:24px;font-size:7.4px}
.env-dl .window{left:18px;top:43px;width:77px;height:37px}
</style>
</head>
<body>

<svg width="0" height="0" style="position:absolute" aria-hidden="true">
  <defs>
    <symbol id="ic-phone" viewBox="0 0 10 10"><path d="M2.2.6 3.8 2.6 2.9 3.8Q4 6 6.2 7.1L7.4 6.2 9.4 7.8 8.3 9.4Q4.6 9.2 2.4 6.8.6 4.6.6 1.7Z"/></symbol>
    <symbol id="ic-fax" viewBox="0 0 10 10"><path d="M2.5.8h4.5l.6.6V4H2.5ZM1 4.4h8v4.8H1Zm1.5 1.4v.9h5v-.9Z"/></symbol>
    <symbol id="ic-mail" viewBox="0 0 10 10"><path d="M.6 2h8.8v6H.6Zm1 .8L5 5.4 8.4 2.8Z"/></symbol>
    <symbol id="ic-web" viewBox="0 0 10 10"><path d="M5 .6a4.4 4.4 0 1 0 0 8.8A4.4 4.4 0 0 0 5 .6Zm-.5 1.1v2.1H2.9a3.5 3.5 0 0 1 1.6-2.1Zm1 0a3.5 3.5 0 0 1 1.6 2.1H5.5Zm-3.8 3h2.8v.6H1.7a3 3 0 0 1 0-.6Zm3.8 0h2.8a3 3 0 0 1 0 .6H5.5Zm-2.6 1.5h1.6v2.1a3.5 3.5 0 0 1-1.6-2.1Zm2.6 0h1.6a3.5 3.5 0 0 1-1.6 2.1Z"/></symbol>
  </defs>
</svg>

<!-- Briefbogen -->
<section class="sheet letter">
  <div class="abs wordmark">Fliesen-Kolbe</div>
  <div class="abs sender"><span class="red">KRMN Kolbe GmbH</span> &nbsp;•&nbsp; Unterfeldbach 48 &nbsp;•&nbsp; 91288 Mühltal</div>
  <div class="abs recipient">Herr<br>Max Mustermann<br>Musterstraße 12<br>12345 Musterstadt</div>
  <div class="abs date">Mühltal, 5. Mai 2025</div>
  <div class="abs subject">Betreff: Briefbogen</div>
  <div class="body">
    <p>Sehr geehrter Herr Mustermann,</p>
    <p>falls Sie keine Probleme haben, diesen Blindtext schnell und zügig zu lesen, können Sie sich glücklich schätzen. Der verantwortliche Art Director, der Ihnen höchstwahr­scheinlich gerade diesen Entwurf präsentiert, versteht sein typografisches Handwerk par excellence.</p>
    <p>Er hat diesen Copyblock weder gestaucht, gezerrt, noch in Versalien oder gar in 6 Punkt Breitgrotesk Outline gesetzt. Er hat ihn ganz einfach lesbar gemacht. Offenbar sogar ziemlich gut, sonst hätten Sie wohl schon einige Zeilen zuvor die Leselust verloren. Beachten Sie nur die Zeilenbreite, die er gewählt hat. Sie ist weder zu lang noch zu kurz gewählt.</p>
    <p>Der dazugehörige Zeilenabstand ist ideal. Ihre Augen haben keinerlei Probleme, vom Ende einer Zeile in die nächste zu gelangen. Um einen solchen Art Director kann man Sie beneiden. Er nutzt den ihm gewährten gestalterischen Freiraum nicht, um sich selbst darzustellen, sondern Sie. Er weiß, daß es Wichtiges über Ihr Unternehmen oder Produkt zu sagen gibt.</p>
    <p>Und dem räumt er großzügig Platz ein. Dieser Mensch hat zweifelsohne nicht am Mäschäßutzets Inschtitut of Gräfick Ahts studiert. Er besitzt keine Bücher von Nora Brandt oder Alma Greve, und wenn doch, ordnet er sie im Regal unter Kunst ein. Statt dessen pflegt er eine liebevoll innige Beziehung zu Büchern von Tessendorf und Ole Aichner. Er liest sie.</p>
    <p>Mit recht freundlichen Grüßen</p>
    <p>Gerd Ulko</p>
  </div>
  <footer class="footer">
    <div class="c1"><span class="red">KRMN Kolbe GmbH</span><br><br>Unterfeldbach 48<br>91288 Mühltal</div>
    <div class="c2">
      <svg class="icons"><use href="#ic-phone"/></svg>09876 / 54 32 100<br>
      <svg class="icons"><use href="#ic-fax"/></svg>09876 / 54 32 177<br>
      <svg class="icons"><use href="#ic-mail"/></svg>post@fliesen-kolbe.de<br>
      <svg class="icons"><use href="#ic-web"/></svg>www.fliesen-kolbe.de
    </div>
    <div class="c3"><span class="b">Bankverbindung</span><br>Raiffeisenbank Talgrund<br>IBAN: DE00 0000 0000 0000 0000 00<br>BIC: GENODEF1TLG</div>
    <div class="c4"><span class="b">Geschäftsführer</span><br>Gerd Ulko<br>HRB 4417 Amtsgericht Talstadt<br>Ust. ID: DE000412786</div>
  </footer>
</section>

<!-- Visitenkarte Vorderseite -->
<section class="card card-front">
  <div class="abs wordmark">Fliesen-Kolbe</div>
</section>

<!-- Visitenkarte Rückseite -->
<section class="card card-back">
  <div class="abs name">Gerd Ulko</div>
  <div class="abs role">Geschäftsführer</div>
  <div class="abs co"><span class="red">KRMN Kolbe GmbH</span><br><br>Unterfeldbach 48<br>91288 Mühltal</div>
  <div class="abs contact">
    <svg class="icons"><use href="#ic-phone"/></svg>09876 / 54 32 100<br>
    <svg class="icons"><use href="#ic-fax"/></svg>09876 / 54 32 177<br>
    <svg class="icons"><use href="#ic-mail"/></svg>post@fliesen-kolbe.de<br>
    <svg class="icons"><use href="#ic-web"/></svg>www.fliesen-kolbe.de
  </div>
</section>

<!-- Übersicht: Briefpapier -->
<section class="sheet sheet-a mini">
  <div class="abs wordmark">Fliesen-Kolbe</div>
  <div class="abs sender"><span class="red">KRMN Kolbe GmbH</span> • Unterfeldbach 48 • 91288 Mühltal</div>
  <footer class="footer">
    <div class="c1"><span class="red">KRMN Kolbe GmbH</span><br><br>Unterfeldbach 48<br>91288 Mühltal</div>
    <div class="c2"><svg class="icons"><use href="#ic-phone"/></svg>09876 / 54 32 100<br><svg class="icons"><use href="#ic-fax"/></svg>09876 / 54 32 177<br><svg class="icons"><use href="#ic-mail"/></svg>post@fliesen-kolbe.de<br><svg class="icons"><use href="#ic-web"/></svg>www.fliesen-kolbe.de</div>
    <div class="c3"><span class="b">Bankverbindung</span><br>Raiffeisenbank Talgrund<br>IBAN: DE00 0000 0000 0000 0000 00<br>BIC: GENODEF1TLG</div>
    <div class="c4"><span class="b">Geschäftsführer</span><br>Gerd Ulko<br>HRB 4417 Amtsgericht Talstadt<br>Ust. ID: DE000412786</div>
  </footer>
</section>

<section class="card mini-front mini">
  <div class="abs wordmark">Fliesen-Kolbe</div>
</section>

<section class="card mini-back mini">
  <div class="abs name">Gerd Ulko</div>
  <div class="abs role">Geschäftsführer</div>
  <div class="abs co"><span class="red">KRMN Kolbe GmbH</span><br><br>Unterfeldbach 48<br>91288 Mühltal</div>
  <div class="abs contact"><svg class="icons"><use href="#ic-phone"/></svg>09876 / 54 32 100<br><svg class="icons"><use href="#ic-fax"/></svg>09876 / 54 32 177<br><svg class="icons"><use href="#ic-mail"/></svg>post@fliesen-kolbe.de<br><svg class="icons"><use href="#ic-web"/></svg>www.fliesen-kolbe.de</div>
</section>

<!-- Übersicht: Notizblock kariert -->
<section class="sheet sheet-b mini">
  <div class="rule" style="top:22px"></div>
  <div class="rule" style="top:30px"></div>
  <div class="abs wordmark">Fliesen-Kolbe</div>
  <div class="grid"></div>
  <footer class="footer">
    <div class="c1"><span class="red">KRMN Kolbe GmbH</span><br><br>Unterfeldbach 48<br>91288 Mühltal</div>
    <div class="c2"><svg class="icons"><use href="#ic-phone"/></svg>09876 / 54 32 100<br><svg class="icons"><use href="#ic-fax"/></svg>09876 / 54 32 177<br><svg class="icons"><use href="#ic-mail"/></svg>post@fliesen-kolbe.de<br><svg class="icons"><use href="#ic-web"/></svg>www.fliesen-kolbe.de</div>
  </footer>
</section>

<!-- Übersicht: Kuvert C4 -->
<section class="envelope env-c4 mini">
  <div class="abs wordmark">Fliesen-Kolbe</div>
  <div class="window">
    <div class="sender abs"><span class="red">KRMN Kolbe GmbH</span> • Unterfeldbach 48 • 91288 Mühltal</div>
    <div class="recipient abs">Herr<br>Max Mustermann<br>Musterstraße 12<br>12345 Musterstadt</div>
  </div>
  <div class="abs web">www.fliesen-kolbe.de</div>
</section>

<!-- Übersicht: Kuvert DIN lang -->
<section class="envelope env-dl mini">
  <div class="abs wordmark">Fliesen-Kolbe</div>
  <div class="window">
    <div class="sender abs"><span class="red">KRMN Kolbe GmbH</span> • Unterfeldbach 48 • 91288 Mühltal</div>
    <div class="recipient abs">Herr<br>Max Mustermann<br>Musterstraße 12<br>12345 Musterstadt</div>
  </div>
</section>

</body>
</html>
```